New Business Card for our Indoor Golf Training Facility

We are looking for designs for a new business card for our indoor golf training facility. Attached is our logo, our logo with our slogan, and here is our elevator pitch (What makes us different from the others) not sure if all the info will fit on one card, maybe you can condense the elevator pitch? here is the info

Elevator Pitch
We work with serious golfers and those that want to be serious golfers…
to make you better, faster, at all phases of the game…
We use the same state-of-the-art technology as professional golfers…
which produces data sets that shows your improvement in real time.
Our facility is available 24/7 to our members, which allows you to improve on your time.

our website: www.birchpinlinks.com

Target Market(s)

Golfers

Font styles to use
Serif
Sans Serif

Colors
ec1f27
f59195
fbd4d5
919191
d3d3d3
1b1b1b

Requirements
Must have
• our logo or our logo with the slogan, elevator pitch (can be condensed or shortened)

```html
<!DOCTYPE html>
<html lang="en">
<head>
<meta charset="utf-8">
<title>Birch Pin Links — Business Card</title>
<link href="https://fonts.googleapis.com/css2?family=Roboto:wght@300;400;500;700;900&display=swap" rel="stylesheet">
<style>
  :root {
    --red: #ec1f27;
    --pink: #f59195;
    --blush: #fbd4d5;
    --grey: #919191;
    --light-grey: #d3d3d3;
    --ink: #1b1b1b;
    --text: #555555;
    --white: #ffffff;
    --stage: #e9e6e1;
  }
  * { box-sizing: border-box; margin: 0; padding: 0; }
  html, body { width: 1200px; height: 911px; overflow: hidden; }
  body {
    background: var(--stage);
    font-family: "Roboto", Arial, sans-serif;
    position: relative;
  }
  .card {
    position: absolute;
    width: 560px;
    height: 320px;
    border-radius: 16px;
    overflow: hidden;
    box-shadow: 0 10px 28px rgba(0,0,0,.18);
  }

  /* ---------- Front ---------- */
  .card--front { left: 50px; top: 110px; background: var(--white); }
  .front__brand {
    position: absolute; left: 36px; top: 122px;
    display: flex; align-items: center; gap: 12px;
  }
  .brand-mark {
    width: 44px; height: 44px; border-radius: 50%;
    border: 3px solid var(--red); flex: none;
  }
  .brand-name { color: var(--red); font-weight: 700; font-size: 30px; line-height: 1; white-space: nowrap; }
  .brand-slogan { color: var(--red); font-size: 11px; margin-top: 5px; white-space: nowrap; }
  .front__divider {
    position: absolute; left: 318px; top: 60px; width: 1px; height: 150px;
    background: var(--light-grey);
  }
  .front__contact { position: absolute; left: 338px; top: 70px; color: var(--ink); }
  .contact-name { color: var(--red); font-weight: 700; font-size: 22px; }
  .contact-role { font-weight: 500; font-size: 13px; margin-top: 2px; }
  .contact-address { color: var(--text); font-size: 12px; line-height: 1.5; margin-top: 12px; }
  .contact-line {
    display: flex; align-items: center; gap: 8px;
    color: var(--text); font-size: 12px; margin-top: 6px;
  }
  .contact-line svg { width: 11px; height: 11px; fill: var(--red); flex: none; }
  .front__band {
    position: absolute; left: 0; bottom: 0; width: 100%; height: 40px;
    background: var(--red);
  }
  .front__band-end {
    position: absolute; right: 0; top: 0; width: 70px; height: 100%;
    background: var(--ink);
  }
  .front__band-dot {
    position: absolute; right: 59px; top: 9px; width: 22px; height: 22px;
    border-radius: 50%; border: 2px solid var(--white); background: var(--red);
  }
  .front__web {
    position: absolute; left: 120px; top: 0; line-height: 40px;
    color: var(--white); font-size: 14px; letter-spacing: 3px;
  }

  /* ---------- Back ---------- */
  .card--back { left: 590px; top: 480px; background: var(--ink); }
  .back__brand {
    position: absolute; left: 0; right: 0; top: 34px;
    display: flex; justify-content: center; align-items: center; gap: 14px;
  }
  .back__brand .brand-mark { width: 56px; height: 56px; }
  .back__brand .brand-name { font-size: 38px; }
  .back__brand .brand-slogan { font-size: 13px; }
  .back__band {
    position: absolute; left: 0; bottom: 0; width: 100%; height: 168px;
    background: var(--red);
  }
  .pitch-label {
    position: absolute; left: 50%; top: -13px; transform: translateX(-50%);
    background: var(--white); color: var(--ink);
    font-weight: 900; font-size: 14px; letter-spacing: .5px;
    padding: 5px 16px; border-radius: 4px; white-space: nowrap;
  }
  .pitch-text {
    position: absolute; left: 24px; right: 24px; top: 26px;
    color: var(--white); text-align: center;
    font-size: 11.5px; line-height: 1.55; font-weight: 500;
  }
  .pitch-social {
    position: absolute; left: 50%; bottom: 12px; transform: translateX(-50%);
    display: flex; gap: 6px;
  }
  .pitch-social span {
    width: 16px; height: 16px; border-radius: 50%; background: var(--white);
  }
</style>
</head>
<body>

<section class="card card--front" aria-label="Business card front">
  <div class="front__brand">
    <div class="brand-mark"></div>
    <div>
      <div class="brand-name">Birch Pin Links</div>
      <div class="brand-slogan">Practice Smart. Play Sharp. Score Lower.</div>
    </div>
  </div>
  <div class="front__divider"></div>
  <div class="front__contact">
    <div class="contact-name">Daniel Reyes</div>
    <div class="contact-role">CEO/Founder</div>
    <div class="contact-address">1480 W. Alder Rd. Unit B4<br>Fairmont, OH 45310</div>
    <div class="contact-line">
      <svg viewBox="0 0 24 24"><path d="M6.6 10.8a15.1 15.1 0 0 0 6.6 6.6l2.2-2.2a1 1 0 0 1 1-.25 11.4 11.4 0 0 0 3.6.57 1 1 0 0 1 1 1V20a1 1 0 0 1-1 1A17 17 0 0 1 3 4a1 1 0 0 1 1-1h3.5a1 1 0 0 1 1 1c0 1.25.2 2.45.57 3.57a1 1 0 0 1-.25 1z"/></svg>
      555-210-3876
    </div>
    <div class="contact-line">
      <svg viewBox="0 0 24 24"><path d="M2 5h20v14H2zm2 2v.5l8 5 8-5V7l-8 5z"/></svg>
      info@birchpinlinks.com
    </div>
  </div>
  <div class="front__band">
    <div class="front__web">www.birchpinlinks.com</div>
    <div class="front__band-end"></div>
    <div class="front__band-dot"></div>
  </div>
</section>

<section class="card card--back" aria-label="Business card back">
  <div class="back__brand">
    <div class="brand-mark"></div>
    <div>
      <div class="brand-name">Birch Pin Links</div>
      <div class="brand-slogan">Practice Smart. Play Sharp. Score Lower.</div>
    </div>
  </div>
  <div class="back__band">
    <div class="pitch-label">ELEVATOR PITCH:</div>
    <p class="pitch-text">
      We coach committed golfers and those who want to become committed golfers…
      to sharpen every part of your game, quicker…
      We train with the same launch-monitor systems the tour players rely on…
      which builds clear reports that track your progress as you swing.
      Our bays stay open around the clock for members, so you can practise whenever it suits you.
    </p>
    <div class="pitch-social"><span></span><span></span></div>
  </div>
</section>

</body>
</html>
```